KBT Business Cards

We require business cards for our business. We would like a matte black back to the card, with our logo centred in the middle. The front side of the card is open to design.

Target Market(s)

Clients looking for legal services (professional)

Industry/Entity Type

Legal

Contact Information for Business Card

Doran Kelbrath
Partner
Mobile: 0461 738 524
Email: doran@kbtlaw.co
Website: www.kbtlaw.co
Level 3, 118 Wendmore Street
Sydney NSW 2000

Font styles to use
Other font styles liked:
• Avenir

Colors
f04a50
ffffff
1b1b1b

Requirements
Must have
• Black back with logo included in the centre of the card.
• Our font is Avenir.

```html
<!DOCTYPE html>
<html lang="en">
<head>
<meta charset="utf-8">
<title>Kelbrath Tamsin Legal – Business Cards</title>
<link rel="stylesheet" href="https://fonts.googleapis.com/css2?family=Montserrat:wght@400;600;700&display=swap">
<style>
  :root {
    --stage: #1c1c1c;
    --card-front: #e8e8e8;
    --card-back: #101010;
    --ink: #1b1b1b;
    --accent: #c01f45;
    --emboss: #262626;
  }
  * { box-sizing: border-box; margin: 0; padding: 0; }
  html, body {
    width: 1200px; height: 1200px; overflow: hidden;
    background: var(--stage);
    font-family: "Montserrat", "Avenir", sans-serif;
  }
  .card {
    position: absolute; left: 228px; width: 744px; height: 424px;
  }
  .card--front { top: 136px; background: var(--card-front); color: var(--ink); }
  .card--back { top: 640px; background: var(--card-back); }

  .brand {
    position: absolute; left: 0; right: 0;
    display: flex; align-items: center; justify-content: center; gap: 26px;
  }
  .card--front .brand { top: 76px; }
  .card--back .brand { top: 150px; }
  .brand__mark { width: 62px; height: 62px; background: var(--accent); }
  .brand__name {
    font-weight: 700; font-size: 32px; line-height: 35px;
    text-transform: uppercase; color: var(--ink);
  }
  .card--back .brand__mark { background: var(--emboss); }
  .card--back .brand__name { color: var(--emboss); }

  .person {
    position: absolute; top: 238px; left: 0; right: 0; text-align: center;
  }
  .person__name { font-weight: 600; font-size: 23px; color: var(--accent); letter-spacing: 0.5px; }
  .person__role { font-weight: 400; font-size: 17px; margin-top: 2px; }
  .divider { width: 44px; height: 4px; background: var(--accent); margin: 14px auto 0; }

  .contact {
    position: absolute; top: 323px; left: 0; right: 0; text-align: center;
    font-size: 17.5px; line-height: 31px; letter-spacing: 0.2px;
  }
  .contact__site { color: var(--accent); }
</style>
</head>
<body>
  <section class="card card--front">
    <div class="brand">
      <div class="brand__mark"></div>
      <div class="brand__name">Kelbrath<br>Tamsin<br>Legal</div>
    </div>
    <div class="person">
      <div class="person__name">Doran Kelbrath</div>
      <div class="person__role">Partner</div>
      <div class="divider"></div>
    </div>
    <div class="contact">
      <p>Level 3, 118 Wendmore Street, Sydney NSW 2000</p>
      <p>0461 738 524 / doran@kbtlaw.co / www.<span class="contact__site">kbtlaw</span>.co</p>
    </div>
  </section>

  <section class="card card--back">
    <div class="brand">
      <div class="brand__mark"></div>
      <div class="brand__name">Kelbrath<br>Tamsin<br>Legal</div>
    </div>
  </section>
</body>
</html>
```